Moravel Aesthetic Doctor

I require an elegant, luxurious looking business card for my aesthetic business. I am a doctor and that will set me aside from competitors. I am planning to provide home and spa based treatments to clients with high expectations. I have attached my logo.

```html
<!DOCTYPE html>
<html lang="en">
<head>
<meta charset="utf-8">
<title>Moravel Aesthetic Doctor – Business Card</title>
<link href="https://fonts.googleapis.com/css2?family=Arimo:wght@400;700&family=Cormorant+Garamond:wght@300;400&display=swap" rel="stylesheet">
<style>
  :root {
    --backdrop: #a8a8a8;
    --sky: #7cc8ec;
    --paper: #ffffff;
    --ink-grey: #8e8f92;
    --ink-blue: #5bbde9;
    --swirl: #eef0f2;
  }
  * { box-sizing: border-box; margin: 0; padding: 0; }
  html, body { width: 1200px; height: 900px; overflow: hidden; }
  body { background: var(--backdrop); position: relative; font-family: "Arimo", Arial, sans-serif; }

  .card { position: absolute; width: 560px; height: 320px; border-radius: 28px; overflow: hidden; box-shadow: 0 10px 22px rgba(0,0,0,.35); }

  /* Front: photo collage */
  .card--front { left: 50px; top: 110px; background: var(--sky); }
  .collage { position: absolute; left: 96px; top: 30px; width: 370px; height: 260px; background: var(--paper); padding: 3px; display: grid; grid-template-columns: repeat(3, 1fr); grid-template-rows: repeat(2, 1fr); gap: 3px; }
  .collage__photo { width: 100%; height: 100%; }
  .photo--facial { background: linear-gradient(135deg, #5a4538, #e8c3b4 60%, #f1d6cf); }
  .photo--towels { background: linear-gradient(160deg, #d7d8d9, #bfc1c3 55%, #8a6a48); }
  .photo--candles { background: radial-gradient(circle at 55% 40%, #f7d68a, #c78634 45%, #6b4a2a); }
  .photo--diffuser { background: linear-gradient(150deg, #f2efec, #d8d2cd 55%, #c86a3c 80%, #c04fa8); }
  .photo--oils { background: linear-gradient(140deg, #efeeec, #dcdad6 55%, #3a3a3a); }
  .photo--massage { background: linear-gradient(150deg, #a8755a, #6a4634 45%, #2f6f96 80%, #e9f1f6); }

  /* Back: contact side */
  .card--back { left: 590px; top: 470px; background: var(--paper); }
  .card__swirl { position: absolute; inset: 0; background: radial-gradient(ellipse 70% 90% at 75% 35%, var(--swirl), rgba(255,255,255,0) 70%); }

  .brand { position: absolute; left: 40px; top: 42px; display: flex; align-items: center; gap: 18px; }
  .brand__circle { width: 78px; height: 78px; border-radius: 50%; border: 2px solid var(--ink-blue); }
  .brand__name { font-family: "Cormorant Garamond", Georgia, serif; font-weight: 300; font-size: 56px; letter-spacing: 6px; color: var(--ink-grey); line-height: 1; }
  .brand__tagline { font-family: "Cormorant Garamond", Georgia, serif; font-weight: 400; font-size: 21px; letter-spacing: 3px; color: var(--ink-blue); margin-top: 4px; }

  .doctor { position: absolute; left: 40px; top: 160px; }
  .doctor__name { font-weight: 700; font-size: 26px; color: var(--ink-grey); }
  .doctor__letters { font-weight: 400; font-size: 13px; color: var(--ink-blue); margin-left: 4px; }
  .doctor__diploma { font-size: 15px; color: var(--ink-blue); margin-top: 2px; }

  .contacts { position: absolute; left: 40px; top: 228px; list-style: none; }
  .contacts__item { display: flex; align-items: center; gap: 10px; font-size: 15px; color: var(--ink-grey); height: 22px; }
  .contacts__icon { width: 15px; height: 15px; }

  .social { position: absolute; right: 32px; top: 36px; display: flex; align-items: center; gap: 6px; font-size: 12px; color: var(--ink-grey); }
  .social__dot { width: 12px; height: 12px; border-radius: 50%; background: var(--ink-blue); }
</style>
</head>
<body>

<section class="card card--front" aria-label="Card front">
  <div class="collage">
    <div class="collage__photo photo--facial" role="img" aria-label="Photo of a gloved facial treatment"></div>
    <div class="collage__photo photo--towels" role="img" aria-label="Photo of rolled towels and a candle"></div>
    <div class="collage__photo photo--candles" role="img" aria-label="Photo of lit candles, towels and a flower"></div>
    <div class="collage__photo photo--diffuser" role="img" aria-label="Photo of a reed diffuser and flowers"></div>
    <div class="collage__photo photo--oils" role="img" aria-label="Photo of serum bottles and a clay mask bowl"></div>
    <div class="collage__photo photo--massage" role="img" aria-label="Photo of a relaxing shoulder massage"></div>
  </div>
</section>

<section class="card card--back" aria-label="Card back">
  <div class="card__swirl" role="img" aria-label="Soft grey flowing background pattern"></div>

  <div class="social"><span class="social__dot"></span>@moravel</div>

  <div class="brand">
    <span class="brand__circle"></span>
    <div>
      <div class="brand__name">MORAVEL</div>
      <div class="brand__tagline">AESTHETIC DOCTOR</div>
    </div>
  </div>

  <div class="doctor">
    <div class="doctor__name">Dr Elena Varga<span class="doctor__letters">MRCPCH MD</span></div>
    <div class="doctor__diploma">Australasian Diploma of Aesthetic Medicine</div>
  </div>

  <ul class="contacts">
    <li class="contacts__item">
      <svg class="contacts__icon" viewBox="0 0 24 24"><path fill="#5bbde9" d="M6.6 10.8a15 15 0 0 0 6.6 6.6l2.2-2.2a1 1 0 0 1 1-.25 11.4 11.4 0 0 0 3.6.57 1 1 0 0 1 1 1V20a1 1 0 0 1-1 1A17 17 0 0 1 3 4a1 1 0 0 1 1-1h3.5a1 1 0 0 1 1 1c0 1.25.2 2.45.57 3.6a1 1 0 0 1-.25 1z"/></svg>
      0800 555 019
    </li>
    <li class="contacts__item">
      <svg class="contacts__icon" viewBox="0 0 24 24"><rect x="2" y="5" width="20" height="14" rx="1" fill="#5bbde9"/><path d="M2.5 5.5 12 13l9.5-7.5" fill="none" stroke="#fff" stroke-width="1.6"/></svg>
      elena@moravel.co.nz
    </li>
    <li class="contacts__item">
      <svg class="contacts__icon" viewBox="0 0 24 24" fill="none" stroke="#5bbde9" stroke-width="2"><circle cx="12" cy="12" r="9.5"/><ellipse cx="12" cy="12" rx="4" ry="9.5"/><path d="M2.5 12h19M4 7h16M4 17h16"/></svg>
      www.moravel.co.nz
    </li>
  </ul>
</section>

</body>
</html>
```